Corvana Tongue Works, LLC

We need a business card that includes information about our business and conveys a reliable business that provides document translation services and interpreters for a variety of corporate and individual clients. We want to come across as professional, reliable, yet approachable. It should include the following on one side:

ESL / ENL Language Classes, Private Lessons, and Online Tutors
PLEXA Training and Testing
Translating & Interpreting Services
Contact us about Over-the-Phone Interpreting in over 200 languages
24/7/365
www.corvanatongue.example

The other side should include (555) 481-3062

Rhoda Pelling, President
482 Garnet Ave., Ste. 219
Indianapolis, IN 40917

Please add USA as part of the address. Also, please add rmpelling@corvanatongueworks.example as the e-mail address. Thank you.

Target Market(s)

Business professionals, their families, the international community

Industry/Entity Type

Business

Contact Information for Business Card

24/7/365
www.corvanatongue.example

(555) 481-3062

Rhoda Pelling, President
482 Garnet Ave., Ste. 219
Indianapolis, IN 40917
USA

Font styles to use
Sans Serif

Colors

Designer to choose colors to be used in the design.

Requirements
Must have
• See project description
• e-mail address and web address
• Phone number
Nice to have
• a globe
• physical address
Should not have
• Should not have the same color scheme as other agencies in our market in Indiana unless it is blue and black. No purple or yellow.

```html
<!DOCTYPE html>
<html lang="en">
<head>
<meta charset="utf-8">
<title>Corvana Tongue Works — Business Card</title>
<link href="https://fonts.googleapis.com/css2?family=Work+Sans:wght@400;500;600&display=swap" rel="stylesheet">
<style>
  :root {
    --stage: #2b2b2d;
    --card: #0b0c0d;
    --blue: #2a95d8;
    --white: #ffffff;
  }
  * { box-sizing: border-box; margin: 0; padding: 0; }
  html, body {
    width: 1200px; height: 900px; overflow: hidden;
    background: var(--stage);
    font-family: "Work Sans", Arial, sans-serif;
  }
  .card {
    position: absolute; left: 250px;
    width: 700px; height: 400px;
    background: var(--card);
    border-radius: 22px;
    overflow: hidden;
    color: var(--white);
  }
  .card--services { top: 38px; }
  .card--contact { top: 466px; }

  /* brand lockup */
  .brand { display: flex; align-items: center; gap: 16px; }
  .brand__dot { width: 70px; height: 70px; border-radius: 50%; flex: none; }
  .brand__name { font-weight: 500; font-size: 30px; line-height: 1.0; letter-spacing: 0.5px; }

  /* services side */
  .card--services .brand { position: absolute; left: 190px; top: 52px; }
  .card--services .brand__dot { background: var(--white); width: 84px; height: 84px; }
  .card--services .brand__name { color: var(--blue); font-size: 34px; }
  .services {
    position: absolute; left: 0; right: 0; top: 170px;
    text-align: center; font-size: 15.5px; line-height: 1.35; font-weight: 500;
  }
  .services__rule { width: 560px; height: 1.5px; background: var(--blue); margin: 12px auto 10px; }

  /* contact side */
  .card--contact .brand { position: absolute; left: 40px; top: 34px; }
  .card--contact .brand__dot { background: var(--blue); }
  .card--contact .brand__name { color: var(--white); }
  .contact__rule {
    position: absolute; left: 40px; right: 132px; top: 200px;
    height: 1.5px; background: var(--blue);
  }
  .contact__list {
    position: absolute; left: 40px; top: 214px;
    list-style: none; font-size: 16px; line-height: 24px;
  }
  .contact__list li { display: flex; align-items: center; gap: 10px; }
  .contact__list svg { width: 14px; height: 14px; flex: none; }
  .person__name {
    position: absolute; right: 132px; top: 150px;
    color: var(--blue); font-size: 34px; font-weight: 500;
    letter-spacing: 1px; text-transform: uppercase; line-height: 44px;
  }
  .person__role {
    position: absolute; right: 132px; top: 206px;
    font-size: 19px; letter-spacing: 0.5px; line-height: 24px;
  }
  .person__bars { position: absolute; right: 70px; top: 154px; display: flex; gap: 8px; }
  .person__bars span { display: block; height: 76px; }
  .bar-white { width: 6px; background: var(--white); }
  .bar-blue { width: 24px; background: var(--blue); }
  .address {
    position: absolute; right: 132px; top: 298px;
    text-align: right; font-size: 21px; line-height: 1.35; letter-spacing: 0.5px;
  }
</style>
</head>
<body>

<section class="card card--services" aria-label="Card back: services">
  <div class="brand">
    <span class="brand__dot"></span>
    <span class="brand__name">Corvana Tongue<br>Works, LLC</span>
  </div>
  <div class="services">
    <p>ESL / ENL Language Classes, Private Lessons, and Online Tutors</p>
    <p>PLEXA Training and Testing</p>
    <p>Translating &amp; Interpreting Services</p>
    <div class="services__rule"></div>
    <p>Contact us about Over-the-Phone Interpreting in over 200 languages</p>
    <p>24/7/365</p>
  </div>
</section>

<section class="card card--contact" aria-label="Card front: contact">
  <div class="brand">
    <span class="brand__dot"></span>
    <span class="brand__name">Corvana Tongue<br>Works, LLC</span>
  </div>
  <p class="person__name">Rhoda Pelling</p>
  <div class="contact__rule"></div>
  <p class="person__role">President</p>
  <div class="person__bars" aria-hidden="true">
    <span class="bar-white"></span><span class="bar-blue"></span>
  </div>
  <ul class="contact__list">
    <li>
      <svg viewBox="0 0 16 16" aria-hidden="true"><path d="M4 1.5l2.2 3-1.3 1.6c.9 2 2.5 3.6 4.5 4.5l1.6-1.3 3 2.2-1.2 2.5C7 13.7 2.3 9 1.5 3z" fill="var(--blue)"/></svg>
      (555) 481-3062
    </li>
    <li>
      <svg viewBox="0 0 16 16" aria-hidden="true"><rect x="1.5" y="3.5" width="13" height="9" fill="none" stroke="var(--blue)" stroke-width="1.4"/><path d="M1.5 3.5L8 9l6.5-5.5" fill="none" stroke="var(--blue)" stroke-width="1.4"/></svg>
      rmpelling@corvanatongueworks.example
    </li>
    <li>
      <svg viewBox="0 0 16 16" aria-hidden="true"><g fill="none" stroke="var(--blue)" stroke-width="1.3"><circle cx="8" cy="8" r="6.5"/><ellipse cx="8" cy="8" rx="3" ry="6.5"/><path d="M1.5 8h13M2.5 4.8h11M2.5 11.2h11"/></g></svg>
      www.corvanatongue.example
    </li>
  </ul>
  <p class="address">482 Garnet Ave., Ste. 219<br>Indianapolis, IN 40917 USA</p>
</section>

</body>
</html>
```